Food Trade Show Advertisement

One full-page advertisement sent as a high-resolution .pdf file that is 11.125" w x 14.25" h

Details on the the wording and pictures will be provided
The to include:
Company logo, product photos (to be supplied), wording (to be supplied), Booth number (to be supplied)
Colors - hot pink
Attached is the guidelines for the advertisement

```html
<!DOCTYPE html>
<html lang="en">
<head>
<meta charset="utf-8">
<title>International Food Trade Show</title>
<link rel="stylesheet" href="https://fonts.googleapis.com/css2?family=Courgette&family=Montserrat:wght@500;600;700&display=swap">
<style>
  :root {
    --backdrop: #3a3a3a;
    --paper: #f4f4f6;
    --hot-pink: #e8337f;
    --hot-pink-light: #f25a9c;
    --magenta: #e0168c;
    --deep-berry: #8e1f5a;
    --white: #ffffff;
    --leaf-green: #5bbf45;
    --flour: #e9dcc0;
    --grain: #d8b66d;
  }
  html, body {
    margin: 0;
    width: 1200px;
    height: 1200px;
    overflow: hidden;
    background: var(--backdrop);
  }
  .canvas { display: block; width: 1200px; height: 1200px; }
  .sans { font-family: "Montserrat", sans-serif; }
  .script { font-family: "Courgette", cursive; }
  .kicker { font-weight: 500; font-size: 36px; fill: var(--white); }
  .headline { font-size: 104px; fill: var(--white); }
  .headline-shadow { font-size: 104px; fill: var(--deep-berry); }
  .dates { font-weight: 700; font-size: 46px; fill: var(--white); paint-order: stroke; stroke: var(--deep-berry); stroke-width: 8px; stroke-linejoin: round; }
  .hours { font-weight: 600; font-size: 34px; fill: var(--magenta); }
  .location { font-weight: 600; font-size: 21px; fill: var(--white); }
  .perks { font-weight: 600; font-size: 26px; fill: var(--white); }
  .booth { font-weight: 600; font-size: 27px; fill: var(--magenta); }
  .phone { font-weight: 500; font-size: 36px; fill: var(--white); }
  .brand-name { font-weight: 700; font-size: 24px; fill: var(--magenta); }
  .partner-name { font-weight: 700; font-size: 15px; fill: var(--leaf-green); letter-spacing: 1px; }
</style>
</head>
<body>
<svg class="canvas" viewBox="0 0 1200 1200" xmlns="http://www.w3.org/2000/svg">
  <defs>
    <linearGradient id="pinkField" x1="0" y1="0" x2="1" y2="1">
      <stop offset="0" stop-color="#f25a9c"/>
      <stop offset="0.5" stop-color="#e8337f"/>
      <stop offset="1" stop-color="#ec4a8f"/>
    </linearGradient>
    <linearGradient id="stripe" x1="0" y1="0" x2="1" y2="0">
      <stop offset="0" stop-color="#ffffff" stop-opacity="0"/>
      <stop offset="0.5" stop-color="#ffffff" stop-opacity="0.12"/>
      <stop offset="1" stop-color="#ffffff" stop-opacity="0"/>
    </linearGradient>
    <radialGradient id="flourTone" cx="0.6" cy="0.45" r="0.6">
      <stop offset="0" stop-color="#eadfc6"/>
      <stop offset="0.6" stop-color="#cfcac0"/>
      <stop offset="1" stop-color="#f4f4f6"/>
    </radialGradient>
    <radialGradient id="grainTone" cx="0.5" cy="0.55" r="0.5">
      <stop offset="0" stop-color="#d8b66d"/>
      <stop offset="0.7" stop-color="#e9dcbf"/>
      <stop offset="1" stop-color="#f4f4f6"/>
    </radialGradient>
    <clipPath id="pageClip"><rect x="170" y="52" width="860" height="1096"/></clipPath>
  </defs>

  <g class="page" clip-path="url(#pageClip)">
    <rect class="page-field" x="170" y="52" width="860" height="1096" fill="url(#pinkField)"/>
    <g class="page-sheen">
      <polygon points="560,52 700,52 1030,420 1030,560" fill="url(#stripe)"/>
      <polygon points="170,560 170,680 1030,1160 1030,1040" fill="url(#stripe)"/>
      <polygon points="170,760 170,840 760,1148 640,1148" fill="url(#stripe)"/>
    </g>

    <path class="hero-panel" d="M170,52 L884,52 C930,200 905,420 725,522 C585,598 330,566 170,466 Z"
          fill="var(--paper)" stroke="var(--magenta)" stroke-width="4"/>
    <rect class="hero-photo" x="217" y="143" width="534" height="323" rx="60" fill="url(#flourTone)"
          role="img" aria-label="Product photo: cloth sack spilling faba bean flour"/>

    <circle class="brand-badge" cx="877" cy="261" r="93" fill="var(--paper)" stroke="var(--magenta)" stroke-width="4"/>
    <text class="sans brand-name" x="877" y="270" text-anchor="middle">Bella Bean</text>

    <circle class="product-badge" cx="823" cy="469" r="124" fill="var(--paper)" stroke="var(--magenta)" stroke-width="4"/>
    <circle cx="823" cy="474" r="100" fill="url(#grainTone)"
            role="img" aria-label="Product photo: pile of textured faba bean protein"/>

    <text class="sans kicker" x="211" y="624">International</text>
    <text class="script headline-shadow" x="603" y="746" text-anchor="middle">Food Trade Show</text>
    <text class="script headline" x="600" y="742" text-anchor="middle">Food Trade Show</text>

    <text class="sans dates" x="600" y="814" text-anchor="middle">20th June - 27th June</text>

    <circle cx="428" cy="867" r="5" fill="var(--white)"/>
    <circle cx="775" cy="867" r="5" fill="var(--white)"/>
    <rect class="hours-pill" x="460" y="843" width="282" height="46" rx="23" fill="var(--white)" stroke="var(--deep-berry)" stroke-width="2"/>
    <text class="sans hours" x="601" y="878" text-anchor="middle">10 am - 9 pm</text>

    <text class="sans location" x="603" y="924" text-anchor="middle">Location: Place Your Location Here</text>

    <polygon class="perks-ribbon" points="397,947 810,947 795,967 810,987 397,987 412,967"
             fill="var(--deep-berry)" stroke="var(--white)" stroke-width="1.5"/>
    <text class="sans perks" x="603" y="977" text-anchor="middle">Free Entry - Free Parking</text>

    <polygon class="booth-tab" points="170,1018 440,1018 460,1053 170,1053" fill="var(--white)"/>
    <text class="sans booth" x="211" y="1046">Booth No: 123</text>

    <g class="phone-icon" fill="none" stroke="var(--white)" stroke-width="2">
      <circle cx="233" cy="1085" r="19"/>
      <path d="M226,1075 l5,-1 3,6 -3,3 c2,4 4,6 8,8 l3,-3 6,3 -1,5 c-12,1 -22,-9 -21,-21 z" fill="var(--white)" stroke="none"/>
    </g>
    <text class="sans phone" x="267" y="1099">123 123 123</text>

    <g class="partner-mark">
      <circle cx="916" cy="1040" r="26" fill="var(--leaf-green)"/>
      <text class="sans partner-name" x="916" y="1093" text-anchor="middle">GREENMEADOW</text>
    </g>
  </g>
</svg>
</body>
</html>
```